I would like a single page website for Skyward Rentals Pacific. In the file list provided there is basic information to be included as well as our logo with colors, fonts and images to be included.
Site must be very simple and be able to be loaded onto smart phones etc very quickly.
Site needs to be very smart in appearance

Target Market(s)

All prospective drone customers from Police to Parties.

Industry/Entity Type

Hire

Requirements
Must have
• Must have variation of color schemes supplied
Nice to have
• Must be very eye catching without going over the top
Should not have
• Anything slow to load.

```html
<!DOCTYPE html>
<html lang="en">
<head>
<meta charset="utf-8">
<title>Skyward Rentals Pacific</title>
<link rel="stylesheet" href="https://fonts.googleapis.com/css2?family=PT+Sans:wght@400;700&family=Share+Tech+Mono&family=Roboto:wght@400;500;700&display=swap">
<style>
:root{
  --green:#78b720;
  --green-dark:#5f9a14;
  --green-light:#8fcb2c;
  --hero:#5c5b60;
  --hero-light:#69686d;
  --ink:#222222;
  --muted:#555555;
  --panel:#f1f1f1;
  --section:#efefef;
  --footer:#1d1d1d;
  --white:#ffffff;
}
*{box-sizing:border-box;margin:0;padding:0}
html,body{width:1200px;height:2311px;overflow:hidden}
body{position:relative;background:var(--white);font-family:"PT Sans",Arial,sans-serif;color:var(--ink)}
h1,h2,h3{font-weight:400}
.abs{position:absolute}

/* header */
.site-header{left:0;top:0;width:1200px;height:108px;background:var(--white);border-bottom:1px solid #ddd}
.brand{left:74px;top:44px;display:flex;align-items:center;gap:10px}
.brand-dot{width:16px;height:16px;border-radius:50%;background:var(--green)}
.brand-name{font-weight:700;font-size:21px;color:var(--green);line-height:1}
.main-nav{left:510px;top:0;height:108px}
.main-nav a{position:absolute;top:0;display:flex;align-items:center;height:108px;font-family:"Roboto",sans-serif;font-weight:400;font-size:12px;color:#222;text-decoration:none;letter-spacing:.3px;white-space:nowrap}
.main-nav .home{left:0;background:var(--green);color:var(--white);width:75px;justify-content:center}
.nav-about{left:104px}
.nav-services{left:212px}
.nav-testimonials{left:310px}
.nav-work{left:433px}
.nav-contact{left:537px}

/* hero */
.hero{left:0;top:108px;width:1200px;height:508px;background:var(--hero);overflow:hidden}
.hero-shade{left:0;top:0}
.hero-title{left:77px;top:110px;font-family:"Share Tech Mono",monospace;font-size:32px;line-height:46px;letter-spacing:3px;color:var(--white)}
.hero-text{left:77px;top:277px;width:490px;font-size:13px;line-height:23px;color:#d6d6d8}
.hero-arrows{left:75px;top:367px;display:flex;gap:4px}
.hero-arrow{width:40px;height:40px;border-radius:50%;background:#1e1e1e;display:flex;align-items:center;justify-content:center}
.hero-drone{left:578px;top:123px;width:570px;height:316px;border-radius:6px;background:radial-gradient(ellipse at 50% 50%,#f2f2f2 0%,#d6d6d6 45%,rgba(92,91,96,0) 72%)}

/* finder */
.finder{left:290px;top:665px;width:620px;height:139px;background:var(--panel)}
.finder-title{left:0;top:26px;width:620px;text-align:center;font-size:27px;letter-spacing:1px;color:#222}
.finder-select{left:29px;top:76px;width:413px;height:40px;background:var(--white);border:1px solid #e2e2e2;font-size:13px;color:#777;padding:0 16px;display:flex;align-items:center;justify-content:space-between}
.finder-submit{left:452px;top:76px;width:138px;height:40px;background:var(--green);color:var(--white);font-family:"Roboto",sans-serif;font-weight:500;font-size:14px;letter-spacing:.5px;display:flex;align-items:center;justify-content:center}

/* services */
.service{width:268px;height:268px;border-radius:50%;background:radial-gradient(circle at 50% 40%,var(--green-light),var(--green) 70%,var(--green-dark));border:3px solid #dcdcdc;box-shadow:0 0 0 1px #eee;text-align:center;color:var(--white)}
.service-icon{position:absolute;left:0;top:28px;width:100%;display:flex;justify-content:center}
.service-title{position:absolute;left:0;top:94px;width:100%;font-family:"Roboto",sans-serif;font-weight:500;font-size:21px;color:#111}
.service-text{position:absolute;left:34px;top:134px;width:194px;font-size:13.5px;line-height:20px}
.service-more{position:absolute;left:0;top:225px;width:100%;font-size:12px;color:#c3e88d}
.services-prev{left:84px;top:958px}
.services-next{left:1088px;top:958px}

/* welcome */
.welcome{left:0;top:1163px;width:1200px;height:636px;background:var(--section)}
.section-title{width:1200px;left:0;text-align:center;font-size:29px;letter-spacing:.5px;color:#222}
.section-rule{left:553px;width:94px;height:4px;background:var(--green)}
.welcome-text{left:123px;top:136px;width:955px;text-align:center;font-size:13px;line-height:24px;color:#333}
.learn-more{left:536px;top:220px;width:131px;height:39px;background:var(--green);color:var(--white);font-size:13px;display:flex;align-items:center;justify-content:center}
.video{left:290px;top:296px;width:620px;height:291px;background:linear-gradient(180deg,#3d3b38 0%,#4a443a 55%,#5a4e3a 100%)}
.video-play{left:0;top:0;width:620px;height:291px;display:flex;align-items:center;justify-content:center}

/* work */
.work-text{left:0;top:1937px;width:1200px;text-align:center;font-size:13px;line-height:23px;color:#333}
.work-item{top:2007px;width:243px;height:153px}
.work-party{left:74px;background:linear-gradient(135deg,#c76a6a,#e3b36a 50%,#7a6fa8)}
.work-stadium{left:344px;background:linear-gradient(180deg,#1e2f56 0%,#6b6a55 45%,#4f8a45 75%,#8b7a5c 100%)}
.work-wedding{left:613px;background:linear-gradient(160deg,#4d7a2c,#6f9a3a 60%,#d8d1d6)}
.work-house{left:883px;background:linear-gradient(180deg,#8aa1b4 0%,#d59a55 45%,#5d5a3a 100%)}

/* footer */
.site-footer{left:0;top:2224px;width:1200px;height:87px;background:var(--footer)}
.copyright{left:77px;top:34px;font-size:12.5px;color:#cfcfcf}
.social{left:964px;top:30px;display:flex;gap:6px}
.social span{width:28px;height:28px;border-radius:50%;background:var(--white)}
</style>
</head>
<body>

<header class="site-header abs">
  <div class="brand abs"><span class="brand-dot"></span><span class="brand-name">Skyward Rentals Pacific</span></div>
  <nav class="main-nav abs">
    <a class="home" href="#">HOME</a>
    <a class="nav-about" href="#">ABOUT US</a>
    <a class="nav-services" href="#">SERVICES</a>
    <a class="nav-testimonials" href="#">TESTIMONIALS</a>
    <a class="nav-work" href="#">OUR WORK</a>
    <a class="nav-contact" href="#">CONTACT US</a>
  </nav>
</header>

<section class="hero abs">
  <svg class="hero-shade abs" width="1200" height="508" aria-hidden="true">
    <polygon points="0,0 720,0 342,508 0,508" fill="var(--hero-light)"/>
  </svg>
  <div class="hero-drone abs" role="img" aria-label="White camera quadcopter drone"></div>
  <h1 class="hero-title abs">WE GIVE DRONES<br>ON HIRE FOR PARTIES,<br>SURVEILLANCE, SECURITY</h1>
  <p class="hero-text abs">Neque porro quisquam est, qui dolorem ipsum quia dolor sit amet, consectetur, adipisci velit, sed quia non numquam eius modi tempora incidunt ut labore et dolore magnam aliquam quaerat voluptatem.</p>
  <div class="hero-arrows abs">
    <span class="hero-arrow"><svg width="12" height="16"><polyline points="9,2 3,8 9,14" fill="none" stroke="#fff" stroke-width="1.6"/></svg></span>
    <span class="hero-arrow"><svg width="12" height="16"><polyline points="3,2 9,8 3,14" fill="none" stroke="#fff" stroke-width="1.6"/></svg></span>
  </div>
</section>

<section class="finder abs">
  <h2 class="finder-title abs">I NEED A DRONE FOR</h2>
  <div class="finder-select abs"><span>Choose your Application</span><svg width="10" height="6"><polygon points="0,0 10,0 5,6" fill="#666"/></svg></div>
  <div class="finder-submit abs">SUBMIT</div>
</section>

<svg class="services-prev abs" width="16" height="28" aria-hidden="true"><polyline points="13,2 3,14 13,26" fill="none" stroke="#555" stroke-width="3"/></svg>

<article class="service abs" style="left:159px;top:838px">
  <div class="service-icon"><svg width="60" height="50" viewBox="0 0 60 50"><polygon points="30,3 3,27 10,27 30,9 50,27 57,27" fill="#fff"/><polygon points="12,27 30,11 48,27 48,48 36,48 36,34 24,34 24,48 12,48" fill="#fff"/><rect x="42" y="6" width="6" height="12" fill="#fff"/></svg></div>
  <h3 class="service-title">REAL ESTATE</h3>
  <p class="service-text">Neque porro quisquam est, qui dolorem ipsum quia dolor sit amet, consectetur, adipisci velit modi tempora incid.</p>
  <span class="service-more">MORE</span>
</article>

<article class="service abs" style="left:467px;top:838px">
  <div class="service-icon"><svg width="56" height="56" viewBox="0 0 56 56"><circle cx="28" cy="28" r="25" fill="#fff"/><polygon points="28,18 37,25 34,35 22,35 19,25" fill="#222"/><circle cx="28" cy="28" r="25" fill="none" stroke="#222" stroke-width="2"/></svg></div>
  <h3 class="service-title">SPORTING EVENTS</h3>
  <p class="service-text">Neque porro quisquam est, qui dolorem ipsum quia dolor sit amet, consectetur, adipisci velit modi tempora incid.</p>
  <span class="service-more">MORE</span>
</article>

<article class="service abs" style="left:776px;top:838px">
  <div class="service-icon"><svg width="74" height="60" viewBox="0 0 74 60"><circle cx="26" cy="36" r="19" fill="none" stroke="#fff" stroke-width="5"/><circle cx="48" cy="36" r="19" fill="none" stroke="#fff" stroke-width="5"/><polygon points="20,4 32,4 36,10 26,17 16,10" fill="#fff"/></svg></div>
  <h3 class="service-title">WEDDINGS</h3>
  <p class="service-text">Neque porro quisquam est, qui dolorem ipsum quia dolor sit amet, consectetur, adipisci velit modi tempora incid.</p>
  <span class="service-more">MORE</span>
</article>

<svg class="services-next abs" width="16" height="28" aria-hidden="true"><polyline points="3,2 13,14 3,26" fill="none" stroke="#cfcfcf" stroke-width="3"/></svg>

<section class="welcome abs">
  <h2 class="section-title abs" style="top:60px">WELCOME TO OUR SITE</h2>
  <div class="section-rule abs" style="top:104px"></div>
  <p class="welcome-text abs">Neque porro quisquam est, qui dolorem ipsum quia dolor sit amet, consectetur, adipisci velit, sed quia non numquam eius modi tempora incidunt ut labore et dolore magnam aliquam quaerat voluptatem. Neque porro quisquam est, qui dolorem ipsum quia dolor sit amet, consectetur, adipisci velit, sed quia non numquam eius modi tempora incidunt ut labore et dolore magnam aliquam quaerat voluptatem.</p>
  <div class="learn-more abs">LEARN MORE</div>
  <div class="video abs" role="img" aria-label="Video still of a quadcopter drone hovering over a field">
    <div class="video-play abs"><svg width="64" height="64"><circle cx="32" cy="32" r="29" fill="none" stroke="#fff" stroke-width="4"/><polygon points="25,19 46,32 25,45" fill="#fff"/></svg></div>
  </div>
</section>

<h2 class="section-title abs" style="top:1866px">OUR WORK</h2>
<div class="section-rule abs" style="top:1910px"></div>
<p class="work-text abs">SARA certified company and SARA endorsed pilot, with Full Public Liability Insurance. All operating licences are in place and are carried on the operator.<br>All drones are maintained to full SARA&nbsp; compliance standards</p>

<div class="work-item work-party abs" role="img" aria-label="Children at a birthday party with cake"></div>
<div class="work-item work-stadium abs" role="img" aria-label="Aerial view of a packed sports stadium at night"></div>
<div class="work-item work-wedding abs" role="img" aria-label="Wedding couple lying on the grass from above"></div>
<div class="work-item work-house abs" role="img" aria-label="Aerial view of a suburban house at sunset"></div>

<footer class="site-footer abs">
  <p class="copyright abs">Copyright ©2015, Yoursite. All Right Reserved.</p>
  <div class="social abs"><span></span><span></span><span></span><span></span><span></span></div>
</footer>

</body>
</html>
```